Harborline Auto LLC

Car Dealer Customer Service
Address: 2874 Cresthaven Road, Shelbyville, TN 37162
web: www.harborlineautoxq.net
email: harborlineautoxq@mailnest.example
Phone: (931) 555-0148
Phone: (629) 555-0173

```html
<!DOCTYPE html>
<html lang="en">
<head>
<meta charset="utf-8">
<title>Harborline Auto LLC – Business Card</title>
<link rel="stylesheet" href="https://fonts.googleapis.com/css2?family=Montserrat:wght@700&family=Open+Sans:wght@400&display=swap">
<style>
  :root {
    --backdrop: #3b3b3b;
    --card-white: #ffffff;
    --card-black: #161616;
    --brand-blue: #1f7ab8;
    --brand-orange: #efb03b;
    --text-grey: #555555;
  }
  * { box-sizing: border-box; margin: 0; padding: 0; }
  html, body { width: 1200px; height: 801px; overflow: hidden; }
  body {
    background: var(--backdrop);
    font-family: "Open Sans", sans-serif;
    position: relative;
  }
  .card {
    position: absolute;
    top: 252px;
    width: 525px;
    height: 300px;
    box-shadow: 0 10px 24px rgba(0,0,0,0.35);
  }
  .card-front {
    left: 45px;
    background: var(--card-white);
    border-bottom: 3px solid var(--brand-blue);
  }
  .card-back {
    left: 630px;
    background: var(--card-black);
    border-bottom: 2px solid var(--brand-blue);
    display: flex;
    align-items: center;
    justify-content: center;
  }
  .brand-mark {
    display: flex;
    align-items: center;
    gap: 10px;
    font-family: "Montserrat", sans-serif;
    font-weight: 700;
    color: var(--brand-blue);
    text-transform: uppercase;
  }
  .brand-mark .dot {
    border-radius: 50%;
    background: var(--brand-orange);
  }
  .card-front .brand-mark {
    position: absolute;
    top: 52px;
    left: 0; right: 0;
    justify-content: center;
    font-size: 20px;
  }
  .card-front .brand-mark .dot { width: 18px; height: 18px; }
  .card-back .brand-mark { font-size: 34px; letter-spacing: 1px; }
  .card-back .brand-mark .dot { width: 28px; height: 28px; }

  .tagline-row {
    position: absolute;
    top: 128px;
    left: 28px; right: 28px;
    display: flex;
    align-items: center;
    gap: 12px;
  }
  .tagline-row .rule {
    flex: 1;
    height: 1.5px;
    background: var(--brand-orange);
  }
  .tagline {
    font-family: "Montserrat", sans-serif;
    font-weight: 700;
    font-size: 16px;
    color: var(--brand-blue);
    text-transform: uppercase;
    white-space: nowrap;
  }
  .contact-list, .location-list {
    position: absolute;
    bottom: 30px;
    list-style: none;
    font-size: 12.5px;
    line-height: 19px;
    color: var(--text-grey);
  }
  .contact-list { left: 32px; }
  .location-list { right: 32px; text-align: right; }
  .contact-list li { display: flex; align-items: center; gap: 7px; }
  .contact-list svg { width: 11px; height: 11px; fill: var(--brand-blue); flex: none; }
  .location-list .web { color: var(--brand-blue); }
</style>
</head>
<body>
  <section class="card card-front">
    <div class="brand-mark"><span class="dot"></span>Harborline Auto LLC</div>
    <div class="tagline-row">
      <span class="rule"></span>
      <h2 class="tagline">Car Dealer Customer Service</h2>
      <span class="rule"></span>
    </div>
    <ul class="contact-list">
      <li><svg viewBox="0 0 24 24"><path d="M6.6 10.8a15 15 0 0 0 6.6 6.6l2.2-2.2a1 1 0 0 1 1-.25 11.4 11.4 0 0 0 3.6.57 1 1 0 0 1 1 1V20a1 1 0 0 1-1 1A17 17 0 0 1 3 4a1 1 0 0 1 1-1h3.5a1 1 0 0 1 1 1c0 1.25.2 2.45.57 3.57a1 1 0 0 1-.25 1z"/></svg>(931) 555-0148</li>
      <li><svg viewBox="0 0 24 24"><path d="M6.6 10.8a15 15 0 0 0 6.6 6.6l2.2-2.2a1 1 0 0 1 1-.25 11.4 11.4 0 0 0 3.6.57 1 1 0 0 1 1 1V20a1 1 0 0 1-1 1A17 17 0 0 1 3 4a1 1 0 0 1 1-1h3.5a1 1 0 0 1 1 1c0 1.25.2 2.45.57 3.57a1 1 0 0 1-.25 1z"/></svg>(629) 555-0173</li>
      <li><svg viewBox="0 0 24 24"><path d="M2 5h20v14H2zm2 2v.5l8 5 8-5V7l-8 5z"/></svg>harborlineautoxq@mailnest.example</li>
    </ul>
    <ul class="location-list">
      <li>2874 Cresthaven Road</li>
      <li>Shelbyville, TN 37162</li>
      <li class="web">www.harborlineautoxq.net</li>
    </ul>
  </section>

  <section class="card card-back">
    <div class="brand-mark"><span class="dot"></span>Harborline Auto</div>
  </section>
</body>
</html>
```